Hi Designers,

I will need 4 web pages designed. The web page looks like an App (if you click on the logo, or the icon on an iPad, it will take you to the website), but it is still a webpage.

Please check the attachment on this brief to understand what specific pages I need to be designed.

A .PSD (straight-up PhotoShop image) as final deliverable is fine, as long as you give us the exact “web color numbers”.

The design is for desktop and iPad but in a single unified web application, NOT separate web app and (native) iPad app.

Details:

Brightwater Policy Partners is developing a browser-based application for use on any mobile device or desktop. The app will be used by corporations to communicate with their employees regarding legal, regulatory and company requirements for conducting business. The app is known as “Harbor Guidance Portal.” When the user clicks on the icon for Harbor Guidance Portal, they will enter a site full of information that a company deems necessary for the employee to do his/her job. There are several content sections within the site, including a login page, training, policies, forms, news feeds and blogs.

The application has been built using Microsoft .NET, and fully supports CSS-type skinning; it uses traditional page layouts. We are seeking a product logo concept (image), a master application/desktop icon (image), as well as a full color scheme/theme/skin design for all areas of the application (header area, body text, menu bar, etc.) in the form of a CSS. The look should be clean, crisp and professional; nothing cartoony or whimsical. It should be easy to read and “airy”.

We have sketched prototypes for the basic application page layout that we can send as a next step of the process.
Updates

Screen shots have been uploaded to this project.  Please use them to guide your design.

Dear designers,

I apologize for the delay in providing feedback. My partners and I will provide feedback in a few days. Thank you for your patience.

Industry/Entity Type

Business

Font styles to use
Other font styles liked:
• see font on screen shots when uploaded

```html
<!DOCTYPE html>
<html lang="en">
<head>
<meta charset="utf-8">
<title>Harbor Guidance Portal – User Login</title>
<link href="https://fonts.googleapis.com/css2?family=Roboto:wght@400;500&display=swap" rel="stylesheet">
<style>
  :root {
    --bg-center: #0e4f8f;
    --bg-edge: #082c58;
    --panel-top: #0a5aa8;
    --panel-bottom: #072f5f;
    --panel-border: #1a4778;
    --text-light: #ffffff;
    --field-top: #ffffff;
    --field-bottom: #ececec;
    --field-border: #c9d3dd;
    --placeholder: #8a8a8a;
    --button-top: #ea8663;
    --button-bottom: #b64824;
    --link: #2f84d6;
    --footer-text: #1f68bb;
    --mark-blue: #2aa6df;
  }
  * { box-sizing: border-box; margin: 0; padding: 0; }
  html, body { width: 1200px; height: 755px; overflow: hidden; }
  body {
    position: relative;
    font-family: "Roboto", Arial, sans-serif;
    background: radial-gradient(ellipse 75% 70% at 50% 45%, var(--bg-center) 0%, var(--bg-edge) 100%);
    color: var(--text-light);
  }
  .brand-top {
    position: absolute; top: 58px; left: 0; width: 1200px;
    display: flex; justify-content: center; align-items: center; gap: 22px;
  }
  .brand-dot { width: 44px; height: 44px; border-radius: 50%; background: var(--mark-blue); }
  .brand-name { font-size: 19px; font-weight: 400; color: var(--text-light); }

  .login-panel {
    position: absolute; left: 210px; top: 145px; width: 780px; height: 337px;
    background: linear-gradient(to bottom, var(--panel-top) 0%, #08498c 50%, var(--panel-bottom) 100%);
    border: 1px solid var(--panel-border);
    text-align: center;
  }
  .portal-title { margin-top: 19px; font-size: 20px; font-weight: 400; letter-spacing: 0.2px; }
  .login-heading { margin-top: 8px; font-size: 19px; font-weight: 500; letter-spacing: 0.3px; }
  .login-form { display: flex; flex-direction: column; align-items: center; }
  .field {
    width: 395px; height: 52px; margin-top: 14px;
    border: 1px solid var(--field-border); border-radius: 2px;
    background: linear-gradient(to bottom, var(--field-top), var(--field-bottom));
    font-family: inherit; font-size: 15px; text-align: center; color: #333;
  }
  .field:first-of-type { margin-top: 19px; }
  .field::placeholder { color: var(--placeholder); }
  .sign-in {
    width: 204px; height: 49px; margin-top: 13px; border: none; border-radius: 2px;
    background: linear-gradient(to bottom, var(--button-top), var(--button-bottom));
    color: var(--text-light); font-family: inherit; font-size: 18px; font-weight: 500; letter-spacing: 0.6px;
  }
  .login-links { margin-top: 20px; font-size: 13px; color: var(--link); }
  .login-links a { color: var(--link); text-decoration: none; }
  .login-links .divider { margin: 0 6px; }

  .brand-bottom {
    position: absolute; top: 535px; left: 0; width: 1200px;
    display: flex; justify-content: center; align-items: center; gap: 18px;
  }
  .brand-bottom .brand-dot { width: 72px; height: 72px; }
  .brand-bottom .brand-name { font-size: 30px; }

  .floor-shadow {
    position: absolute; top: 655px; left: 100px; width: 1000px; height: 14px;
    background: radial-gradient(ellipse 50% 100% at 50% 0%, rgba(2,18,40,0.55), rgba(2,18,40,0));
  }
  .site-footer {
    position: absolute; top: 694px; left: 0; width: 1200px;
    text-align: center; font-size: 13px; line-height: 21px; color: var(--footer-text);
  }
</style>
</head>
<body>
  <header class="brand-top">
    <span class="brand-dot"></span>
    <span class="brand-name">Novaline Labs</span>
  </header>

  <section class="login-panel">
    <h1 class="portal-title">Harbor Guidance Portal</h1>
    <h2 class="login-heading">USER LOGIN</h2>
    <form class="login-form">
      <input class="field" type="text" placeholder="Username">
      <input class="field" type="password" placeholder="Password">
      <button class="sign-in" type="button">SIGN IN</button>
    </form>
    <p class="login-links">
      <a href="#">Keep me sign in</a><span class="divider">|</span><a href="#">Forgot Password?</a>
    </p>
  </section>

  <div class="brand-bottom">
    <span class="brand-dot"></span>
    <span class="brand-name">Harbor Guidance Portal</span>
  </div>

  <div class="floor-shadow"></div>

  <footer class="site-footer">
    Copyright © 2013. Harbor Guidance Portal<br>
    All Right Reserved
  </footer>
</body>
</html>
```